Business Card Design for Mortgage Broking Business

We need to redesign the business card. Mortgage broking business, doing home loan and commercial loans, existing logo, also QLBT member logo. design style needs to be simple, professional, elegant.

once final, need to setup for a team of different names and contact details.

Industry/Entity Type

Loan

Contact Information for Business Card

Name; Mobile; Email; Address; Tel; Fax; Australian Credit Licence: 618204

```html
<!DOCTYPE html>
<html lang="en">
<head>
<meta charset="utf-8">
<title>Harbourline Finance – Business Card</title>
<link href="https://fonts.googleapis.com/css2?family=Open+Sans:wght@400;600;700&display=swap" rel="stylesheet">
<style>
  :root {
    --backdrop: #e4e4e4;
    --navy: #22338a;
    --navy-deep: #1c2c7c;
    --sky: #1a8fe0;
    --leaf: #7cb832;
    --paper: #ffffff;
    --ink: #24358f;
    --muted: #3b4a9a;
  }
  * { box-sizing: border-box; margin: 0; padding: 0; }
  html, body {
    width: 1200px;
    height: 852px;
    overflow: hidden;
  }
  body {
    background: var(--backdrop);
    font-family: "Open Sans", Arial, sans-serif;
    position: relative;
  }
  .card {
    position: absolute;
    width: 525px;
    height: 300px;
    border-radius: 22px;
    overflow: hidden;
    box-shadow: 0 10px 26px rgba(0, 0, 0, 0.22);
  }

  /* Front */
  .card-front {
    left: 90px;
    top: 110px;
    background: linear-gradient(135deg, var(--navy-deep) 0%, var(--navy) 55%, #2a3f9a 100%);
    display: flex;
    align-items: center;
    justify-content: center;
  }
  .brand {
    display: flex;
    flex-direction: column;
    align-items: center;
    color: var(--paper);
  }
  .brand-name {
    display: flex;
    align-items: center;
    gap: 14px;
    font-weight: 700;
    font-size: 38px;
    letter-spacing: 0.3px;
  }
  .brand-mark {
    width: 30px;
    height: 30px;
    background: var(--leaf);
  }
  .brand-rule {
    width: 100%;
    height: 2px;
    background: currentColor;
    margin: 10px 0 8px;
  }
  .brand-tagline {
    font-weight: 700;
    font-size: 20px;
    letter-spacing: 0.4px;
  }

  /* Back */
  .card-back {
    left: 585px;
    top: 442px;
    background: var(--paper);
  }
  .back-band {
    position: absolute;
    left: 0;
    top: 0;
    bottom: 0;
    width: 40px;
    background: var(--navy);
    border-right: 5px solid var(--sky);
  }
  .back-brand {
    position: absolute;
    right: 28px;
    top: 30px;
    color: var(--ink);
    display: flex;
    flex-direction: column;
    align-items: flex-end;
  }
  .back-brand .brand-name { font-size: 22px; gap: 8px; }
  .back-brand .brand-mark { width: 18px; height: 18px; }
  .back-brand .brand-rule { margin: 5px 0 4px; height: 1.5px; }
  .back-brand .brand-tagline { font-size: 12px; }

  .person {
    position: absolute;
    left: 72px;
    top: 112px;
    color: var(--ink);
  }
  .person-name { font-weight: 700; font-size: 17px; }
  .person-role { font-size: 11.5px; color: var(--muted); margin-top: 2px; }

  .contacts {
    position: absolute;
    left: 72px;
    bottom: 30px;
    list-style: none;
    color: var(--muted);
    font-size: 12.5px;
  }
  .contacts li {
    display: flex;
    align-items: center;
    gap: 8px;
    line-height: 21px;
  }
  .contacts svg { width: 13px; height: 13px; fill: var(--sky); flex: none; }
  .contacts .pair { display: inline-flex; align-items: center; gap: 6px; margin-left: 6px; }

  .member-badge {
    position: absolute;
    right: 30px;
    top: 150px;
    width: 104px;
    height: 36px;
    border: 2px solid var(--navy);
    border-radius: 3px;
    background: linear-gradient(90deg, rgba(124, 184, 50, 0.18), rgba(26, 143, 224, 0.12));
  }
</style>
</head>
<body>

  <section class="card card-front" aria-label="Business card front">
    <div class="brand">
      <div class="brand-name"><span class="brand-mark"></span>Harbourline Finance</div>
      <div class="brand-rule"></div>
      <div class="brand-tagline">Mortgage Planners</div>
    </div>
  </section>

  <section class="card card-back" aria-label="Business card back">
    <div class="back-band"></div>

    <div class="brand back-brand">
      <div class="brand-name"><span class="brand-mark"></span>Harbourline Finance</div>
      <div class="brand-rule"></div>
      <div class="brand-tagline">Mortgage Planners</div>
    </div>

    <div class="person">
      <div class="person-name">Your Long Name</div>
      <div class="person-role">Managing Director</div>
    </div>

    <div class="member-badge" role="img" aria-label="QLBT member badge"></div>

    <ul class="contacts">
      <li>
        <svg viewBox="0 0 24 24" aria-hidden="true"><path d="M12 2a7 7 0 0 0-7 7c0 5 7 13 7 13s7-8 7-13a7 7 0 0 0-7-7zm0 9.5A2.5 2.5 0 1 1 12 6a2.5 2.5 0 0 1 0 5.5z"/></svg>
        Your Commercial or office address
      </li>
      <li>
        <svg viewBox="0 0 24 24" aria-hidden="true"><path d="M6.6 10.8a15 15 0 0 0 6.6 6.6l2.2-2.2a1 1 0 0 1 1-.25 11.4 11.4 0 0 0 3.6.57 1 1 0 0 1 1 1V20a1 1 0 0 1-1 1A17 17 0 0 1 3 4a1 1 0 0 1 1-1h3.5a1 1 0 0 1 1 1c0 1.25.2 2.45.57 3.57a1 1 0 0 1-.25 1z"/></svg>
        00.00.00.0000
        <span class="pair">
          <svg viewBox="0 0 24 24" aria-hidden="true"><path d="M6 3h9l3 3v4h1a2 2 0 0 1 2 2v7a2 2 0 0 1-2 2H5a2 2 0 0 1-2-2v-7a2 2 0 0 1 2-2h1zm2 2v5h8V7h-2V5zm0 9v2h8v-2z"/></svg>
          00.00.00.0000
        </span>
      </li>
      <li>
        <svg viewBox="0 0 24 24" aria-hidden="true"><path d="M3 5h18v14H3zm2 2v.5l7 4.5 7-4.5V7zm0 2.9V17h14V9.9l-7 4.5z"/></svg>
        yourname@yourwebsite.com
      </li>
      <li>
        <svg viewBox="0 0 24 24" aria-hidden="true"><path d="M12 2a10 10 0 1 0 0 20 10 10 0 0 0 0-20zm6.9 9h-3a15 15 0 0 0-1.4-6A8 8 0 0 1 18.9 11zM12 4c.9 1.2 1.8 3.6 1.9 7h-3.8c.1-3.4 1-5.8 1.9-7zM9.5 5a15 15 0 0 0-1.4 6h-3A8 8 0 0 1 9.5 5zm-4.4 8h3a15 15 0 0 0 1.4 6 8 8 0 0 1-4.4-6zM12 20c-.9-1.2-1.8-3.6-1.9-7h3.8c-.1 3.4-1 5.8-1.9 7zm2.5-1a15 15 0 0 0 1.4-6h3a8 8 0 0 1-4.4 6z"/></svg>
        www.yourwebsite.com
      </li>
    </ul>
  </section>

</body>
</html>
```